Carpentry framing business card and logo design

We need a logo that works well with baseball caps, tee shirts and sweat shirts. We are a carpentry framing company specializing in apartment complexes and large residential communities. We work in what is known as the tri state area southeastern Pennsylvania , New Jersey and northern Delaware . We would like to see die signs using the old English letter M and royal blue colors. Also we stress OSHA compliance and safety.

Industry/Entity Type

Residential

Contact Information for Business Card

Valdrick Construction Co Inc
4870 Quillford Lane
Ambler PA 19087
Dale Valdrick
dale1valdrick@norvexmail.com
267-815-0926

```html
<!DOCTYPE html>
<html lang="en">
<head>
<meta charset="utf-8">
<title>Valdrick Construction – Business Card</title>
<link href="https://fonts.googleapis.com/css2?family=Jost:wght@400;500;700&display=swap" rel="stylesheet">
<style>
  :root {
    --backdrop: #d9d6d0;
    --card: #f7f5f0;
    --navy: #1f2a6b;
    --ink: #2b3170;
    --shadow: rgba(0, 0, 0, 0.18);
  }
  * { box-sizing: border-box; margin: 0; padding: 0; }
  html, body {
    width: 1029px;
    height: 1200px;
    overflow: hidden;
    background: var(--backdrop);
    font-family: "Jost", Futura, sans-serif;
  }
  .sheet {
    width: 1029px;
    height: 1200px;
    display: flex;
    flex-direction: column;
    justify-content: space-evenly;
    align-items: center;
  }
  .card {
    position: relative;
    width: 880px;
    height: 503px;
    background: var(--card);
    box-shadow: 0 6px 18px var(--shadow);
  }
  .brand {
    position: absolute;
    left: 70px;
    top: 30px;
    width: 240px;
    height: 100%;
    display: flex;
    flex-direction: column;
    align-items: center;
    justify-content: center;
    color: var(--navy);
    font-weight: 500;
    text-align: center;
  }
  .brand-mark {
    width: 22px;
    height: 22px;
    background: var(--navy);
    margin-bottom: 14px;
  }
  .brand-name { font-size: 38px; letter-spacing: 1px; line-height: 1; }
  .brand-sub { font-size: 17px; letter-spacing: 3px; margin-top: 6px; }
  .divider {
    position: absolute;
    left: 372px;
    top: 88px;
    width: 2px;
    height: 330px;
    background: var(--navy);
  }
  .details {
    position: absolute;
    top: 110px;
    color: var(--ink);
  }
  .details--right { right: 60px; text-align: right; }
  .details--left { left: 420px; text-align: left; }
  .person {
    font-size: 40px;
    font-weight: 700;
    color: var(--navy);
    line-height: 1.1;
    margin-bottom: 14px;
  }
  .address { font-size: 16px; line-height: 1.2; margin-bottom: 20px; }
  .contact {
    font-size: 16px;
    line-height: 1.5;
    display: flex;
    flex-direction: column;
  }
  .contact-row { display: flex; align-items: center; gap: 8px; }
  .details--right .contact-row { justify-content: flex-end; }
  .icon { width: 16px; height: 16px; flex: none; }
  .tagline {
    position: absolute;
    bottom: 58px;
    font-size: 16px;
    color: var(--ink);
  }
  .details--right ~ .tagline { right: 60px; }
  .details--left ~ .tagline { right: 110px; }
</style>
</head>
<body>
<main class="sheet">

  <section class="card">
    <div class="brand">
      <span class="brand-mark"></span>
      <span class="brand-name">VALDRICK</span>
      <span class="brand-sub">CONSTRUCTION</span>
    </div>
    <div class="divider"></div>
    <div class="details details--right">
      <h1 class="person">Dale Valdrick</h1>
      <p class="address">4870 Quillford Lane<br>Quellmont PA 19087</p>
      <div class="contact">
        <span class="contact-row">dale1valdrick@norvexmail.com
          <svg class="icon" viewBox="0 0 16 16"><rect x="1" y="3" width="14" height="10" fill="none" stroke="currentColor" stroke-width="1.5"/><path d="M1 3l7 6 7-6M1 13l5-5M15 13l-5-5" fill="none" stroke="currentColor" stroke-width="1.2"/></svg>
        </span>
        <span class="contact-row">267-815-0926
          <svg class="icon" viewBox="0 0 16 16"><rect x="4" y="1" width="8" height="14" rx="1.5" fill="none" stroke="currentColor" stroke-width="1.5"/><line x1="7" y1="12.5" x2="9" y2="12.5" stroke="currentColor" stroke-width="1.2"/></svg>
        </span>
      </div>
    </div>
    <p class="tagline">OSHA compliance and SAFETY 1st</p>
  </section>

  <section class="card">
    <div class="brand">
      <span class="brand-mark"></span>
      <span class="brand-name">VALDRICK</span>
      <span class="brand-sub">CONSTRUCTION</span>
    </div>
    <div class="divider"></div>
    <div class="details details--left">
      <h1 class="person">Dale Valdrick</h1>
      <p class="address">4870 Quillford Lane<br>Quellmont PA 19087</p>
      <div class="contact">
        <span class="contact-row">
          <svg class="icon" viewBox="0 0 16 16"><rect x="1" y="3" width="14" height="10" fill="none" stroke="currentColor" stroke-width="1.5"/><path d="M1 3l7 6 7-6M1 13l5-5M15 13l-5-5" fill="none" stroke="currentColor" stroke-width="1.2"/></svg>
          dale1valdrick@norvexmail.com
        </span>
        <span class="contact-row">
          <svg class="icon" viewBox="0 0 16 16"><rect x="4" y="1" width="8" height="14" rx="1.5" fill="none" stroke="currentColor" stroke-width="1.5"/><line x1="7" y1="12.5" x2="9" y2="12.5" stroke="currentColor" stroke-width="1.2"/></svg>
          267-815-0926
        </span>
      </div>
    </div>
    <p class="tagline">OSHA compliance and SAFETY 1st</p>
  </section>

</main>
</body>
</html>
```